International Clinical Software Company needs a new business card design

We are looking for a new business card design for our company that has recently expanded into the UK market, making us a multinational company.
After having rebranded our website and produced a new style guide, we are looking for a business card that is creative and attention grabbing, while being consistent with the style and colour scheme used on the new website, www.plumvora.example
We produce care management technology for the aged care market, but the main aspect we aim to communicate is the human element of our software, and the way it assists in providing better care for aged people, and stronger relationships between aged people and the staff that care for them.
Our current business card is a dark green with gold text, which makes the text quite difficult to read, not very aesthetically appealing and the colour scheme looks quite dated.
We would like something fresh and modern, that can still be colourful but doesn't use large blocks of dark colour, and uses the colours within our logo.
Something tying in with the leaves that are used in our logo could work quite nicely, along with the Autumn/Fall colours of soft greens, yellows and reds (also in our existing logo). However also happy to look at fresh, completely out of the box ideas we may not have yet considered.
Target Market(s)
The people that receive this business card work in the aged card or health industry and are either corporate/management level staff or clinical (Registered Nurses, care workers etc.)
Industry/Entity Type
Health Product
Contact Information for Business Card
Company Name - BrindlewayCare
Company locations: United Kingdom, Australia, New Zealand
Staff Details:
Staff name: Derek Mallow
Staff job title: Executive Chairman
Staff email: d.mallow@plumvora.example
Office phone number: 01742 918576
Font styles to use
Other font styles liked:
- Calibri
Requirements
Must have
- Must include the BrindlewayCare brand name in it's current font
- Must include logo (3 leaves in gold circle)
- Must include Business Card Details
Nice to have
- Elements of gold
- White space
- Something autumn themed but not too cliched
Should not have
- No blue - used by a major competitor and we would like to differentiate from them
- Large blocks of dark green colour (the green that appears in our leaves on the logo on our current business card is the background colour and it is far too dark)

```html
<!DOCTYPE html>
<html lang="en">
<head>
<meta charset="utf-8">
<title>BrindlewayCare Business Card</title>
<link href="https://fonts.googleapis.com/css2?family=Carlito:wght@400;700&display=swap" rel="stylesheet">
<style>
  :root {
    --backdrop: #3b322d;
    --card-black: #161616;
    --card-black-soft: #232323;
    --gold: #b9a27a;
    --gold-text: #c9ad78;
    --white: #f4f1ea;
    --leaf-green: #5c8a2c;
    --leaf-yellow: #c7b52a;
    --leaf-red: #b8163f;
  }
  * { box-sizing: border-box; margin: 0; padding: 0; }
  html, body {
    width: 1200px; height: 844px; overflow: hidden;
    background: var(--backdrop);
    font-family: "Carlito", "Calibri", sans-serif;
  }
  .canvas { position: relative; width: 1200px; height: 844px; }

  .card {
    position: absolute;
    width: 520px; height: 300px;
    background: linear-gradient(120deg, var(--card-black) 55%, var(--card-black-soft));
    overflow: hidden;
  }

  /* Details side */
  .card--details { left: 50px; top: 272px; }
  .card__band {
    position: absolute; left: 0; width: 100%; height: 14px;
    background: var(--gold);
  }
  .card__band--top { top: 0; }
  .card__band--bottom { bottom: 0; }
  .card__leaves {
    position: absolute; left: 0; top: 60px; bottom: 14px; width: 150px;
    background: linear-gradient(90deg, var(--leaf-green) 0%, var(--leaf-green) 30%, var(--leaf-yellow) 55%, var(--leaf-red) 85%);
    border-top-right-radius: 100% 70%;
  }
  .details {
    position: absolute; left: 200px; top: 70px; width: 280px;
    color: var(--white);
  }
  .details__name {
    font-weight: 700; font-size: 20px; letter-spacing: 0.5px;
    color: var(--gold-text); text-transform: uppercase;
    padding-bottom: 4px; border-bottom: 1px solid var(--gold);
    display: inline-block; padding-right: 14px;
  }
  .details__title { font-size: 14px; margin-top: 5px; padding-left: 14px; }
  .details__email { font-size: 14px; margin-top: 42px; padding-left: 56px; }
  .details__locations { font-size: 15px; margin-top: 38px; }

  /* Brand side */
  .card--brand { left: 630px; top: 272px; }
  .card__tab {
    position: absolute; width: 22px; height: 40px;
    background: var(--gold);
  }
  .card__tab--right { right: 0; top: 18px; }
  .card__tab--left { left: 0; bottom: 40px; }
  .brand {
    position: absolute; left: 0; right: 0; top: 92px;
    display: flex; flex-direction: column; align-items: center; gap: 16px;
  }
  .brand__mark {
    width: 64px; height: 64px; border-radius: 50%;
    border: 2px solid var(--gold);
  }
  .brand__name {
    font-size: 46px; font-weight: 400; color: var(--gold-text);
    letter-spacing: 1px;
  }
</style>
</head>
<body>
<main class="canvas">
  <section class="card card--details">
    <div class="card__band card__band--top"></div>
    <div class="card__leaves" role="img" aria-label="Illustration of three overlapping autumn leaves in green, yellow and red"></div>
    <div class="details">
      <p class="details__name">Derek Mallow</p>
      <p class="details__title">Executive Chairman</p>
      <p class="details__email">d.mallow@plumvora.example</p>
      <p class="details__locations">United Kingdom, Australia New Zealand</p>
    </div>
    <div class="card__band card__band--bottom"></div>
  </section>

  <section class="card card--brand">
    <div class="card__tab card__tab--right"></div>
    <div class="brand">
      <div class="brand__mark"></div>
      <p class="brand__name">BrindlewayCare</p>
    </div>
    <div class="card__tab card__tab--left"></div>
  </section>
</main>
</body>
</html>
```